Visitenkarten-Design für Fotografen
Zielgruppe
German:
Hey,
ich habe ein Einzelunternehmen, noch im Nebengewerbe, im Bereich der professionellen Motorrad- & vor allem Autofotografie.
Nun möchte ich aber mich dieses Jahr sehr auf die Fotografie konzentrieren und benötige daher schöne, moderne Visitenkarten passend zu meiner Arbeit. Dabei möchte ich dieses Jahr auch noch zur Videografie, in Bezug auf Videos zu schönen Autos, finden und diese in mein Unternehmen mit einfließen lassen.
Hauptsächlich möchte ich mich dabei auf Sportwagen wie Varessini, Kelto XT, Brunvik uvm. konzentrieren. Dabei sind die meisten Kunden halt Privatpersonen, wobei ich in Zukunft auch sehr gerne mit Firmen zusammen arbeiten möchte.
Außerdem bin ich auch oft auf Tuning Treffen in ganz Deutschland anzutreffen, komme aber aus Templin, Brandenburg.
English:
I have a sole proprietorship, still in the ancillary trade, in the field of professional motorcycle & especially car photography.
But now I want to focus very much on photography this year and therefore I need beautiful, modern business cards to match my work. This year I also want to find out about videography, in relation to videos about beautiful cars, and incorporate it into my company.
Mainly I want to focus on sports cars like Varessini, Kelto XT, Brunvik and much more. Most of the customers are private individuals, although I would also like to work with companies in the future.
I am also often present at tuning meetings all over Germany, but I come from Templin, Brandenburg.
Aufgabenstellung
Visitenkarten, die
- modern
- elegant
-zweiseitig
- nicht zu überladen, aber: Instagram, Telefonnummer, Website und Mail sollten drauf sein
- ein Bezug zur Auto / Motorradfotografie sollte da sein, Schwerpunkt ist zu 80% die Auto Fotografie
- two-sided
- not to overload, but: Instagram, phone number, website and mail should be on it, further you're welcome
- a reference to car / motorcycle photography should be there, focus is 80% on car photography
Telefon: 0157 / 38214650
Website: http://lichtkantestudio.example (at the moment http://jonaskerbel.sitebaukasten.example/lichtkantestudio)
Mail: lichtkante.studio@postfach.example

```html
<!DOCTYPE html>
<html lang="de">
<head>
<meta charset="utf-8">
<title>LichtkanteStudio – Visitenkarten</title>
<link rel="stylesheet" href="https://fonts.googleapis.com/css2?family=Montserrat:wght@400;500;600&display=swap">
<style>
:root{
  --black:#000;
  --white:#fff;
  --gold:#e48c1c;
  --gold-deep:#c98420;
  --swatch-flat:#c47f20;
  --grey-band:#e6e6e6;
  --scene-bg:#1b1b1b;
  --scene-card:#141414;
}
*{margin:0;padding:0;box-sizing:border-box}
html,body{width:1200px;height:3000px;overflow:hidden;background:var(--white)}
body{position:relative;font-family:"Montserrat",Arial,sans-serif}
.section{position:absolute;left:0;width:1200px}
.section--white-top{top:0;height:600px;background:var(--white)}
.section--grey{top:600px;height:600px;background:var(--grey-band)}
.section--white-mid{top:1200px;height:600px;background:var(--white)}
.section--dark{top:1800px;height:1200px;background:var(--scene-bg)}

.card{position:absolute;background:var(--black);overflow:hidden;color:var(--white)}
.card--shadow{box-shadow:0 10px 24px rgba(0,0,0,.35)}
.card--gold{color:var(--gold)}
.card--scene{background:var(--scene-card);color:var(--gold-deep);border-radius:2.5em;box-shadow:0 14px 30px rgba(0,0,0,.6)}
.card--lg{width:426px;height:275px;font-size:4.26px}
.card--sm{width:307px;height:198px;font-size:3.07px}
.card--xl{width:628px;height:416px;font-size:6.28px}

.brand-name{position:absolute;left:0;right:0;top:24.5em;text-align:center;font-weight:600;font-size:6.4em;letter-spacing:.02em;line-height:1}
.brand-name{top:3.8em}
.website{position:absolute;left:0;right:0;top:57em;text-align:center;font-weight:600;font-size:2.1em;letter-spacing:.14em}
.website{top:26.8em}

.signature{position:absolute;left:7em;top:24em;width:35em;height:9em;border-radius:1em;background:currentColor;opacity:.22}
.role-title{position:absolute;left:6.6em;top:35em;font-size:2.1em;font-weight:500;letter-spacing:.02em;white-space:nowrap}
.role-title{top:17em;left:3.1em}
.divider{position:absolute;left:48.5em;top:22em;width:.35em;height:20em;background:currentColor}

.contact-list{position:absolute;left:51.5em;top:24em;list-style:none}
.contact-item{display:flex;align-items:center;height:6.6em;font-size:1em}
.contact-item svg{width:2.6em;height:2.6em;flex:none;margin-right:2.8em;fill:currentColor}
.contact-item span{font-size:2.15em;font-weight:500;white-space:nowrap}

.swatch{position:absolute}
.swatch--gradient{background:linear-gradient(115deg,#f7a21a 0%,#f08c00 14%,#fbd7a0 22%,#f09000 30%,#d67a00 44%,#7a3a00 52%,#e88d10 60%,#ffa92a 68%,#d37400 80%,#7b3800 94%,#a85200 100%)}
.swatch--flat{background:var(--swatch-flat)}
</style>
</head>
<body>

<svg width="0" height="0" style="position:absolute">
  <defs>
    <symbol id="icon-home" viewBox="0 0 24 24"><path d="M12 2 1 12h3v10h6v-6h4v6h6V12h3z"/></symbol>
    <symbol id="icon-phone" viewBox="0 0 24 24"><path d="M6.6 10.8a15.1 15.1 0 0 0 6.6 6.6l2.2-2.2c.3-.3.7-.4 1-.2 1.1.4 2.3.6 3.6.6.6 0 1 .4 1 1V20c0 .6-.4 1-1 1C10.6 21 3 13.4 3 4c0-.6.4-1 1-1h3.5c.6 0 1 .4 1 1 0 1.3.2 2.5.6 3.6.1.3 0 .7-.2 1z"/></symbol>
    <symbol id="icon-mail" viewBox="0 0 24 24"><path d="M2 5h20v2l-10 6L2 7zm0 4 10 6 10-6v10H2z"/></symbol>
    <symbol id="icon-dot" viewBox="0 0 24 24"><circle cx="12" cy="12" r="9" fill="none" stroke="currentColor" stroke-width="2.6"/></symbol>
  </defs>
</svg>

<section class="section section--white-top">
  <div class="card card--lg card--shadow" style="left:132px;top:163px">
    <div class="brand-name">LichtkanteStudio</div>
    <div class="website">WWW.LICHTKANTESTUDIO.EXAMPLE</div>
  </div>
  <div class="card card--lg card--shadow" style="left:642px;top:163px">
    <div class="signature" role="img" aria-label="Handschriftliche Unterschrift Jonas Kerbel"></div>
    <div class="role-title">AUTOMOTIVE PHOTOGRAPHER</div>
    <div class="divider"></div>
    <ul class="contact-list">
      <li class="contact-item"><svg><use href="#icon-home"/></svg><span>17389 Uckerfeld, Brandenburg</span></li>
      <li class="contact-item"><svg><use href="#icon-phone"/></svg><span>0157 / 38214650</span></li>
      <li class="contact-item"><svg><use href="#icon-mail"/></svg><span>lichtkante.studio@postfach.example</span></li>
      <li class="contact-item"><svg><use href="#icon-dot"/></svg><span>Lichtkante_Studio</span></li>
    </ul>
  </div>
</section>

<section class="section section--grey">
  <div class="card card--sm card--gold" style="left:70px;top:185px">
    <div class="brand-name">LichtkanteStudio</div>
    <div class="website">WWW.LICHTKANTESTUDIO.EXAMPLE</div>
  </div>
  <div class="card card--sm card--gold" style="left:437px;top:185px">
    <div class="signature" role="img" aria-label="Handschriftliche Unterschrift Jonas Kerbel"></div>
    <div class="role-title">AUTOMOTIVE PHOTOGRAPHER</div>
    <div class="divider"></div>
    <ul class="contact-list">
      <li class="contact-item"><svg><use href="#icon-home"/></svg><span>17389 Uckerfeld, Brandenburg</span></li>
      <li class="contact-item"><svg><use href="#icon-phone"/></svg><span>0157 / 38214650</span></li>
      <li class="contact-item"><svg><use href="#icon-mail"/></svg><span>lichtkante.studio@postfach.example</span></li>
      <li class="contact-item"><svg><use href="#icon-dot"/></svg><span>Lichtkante_Studio</span></li>
    </ul>
  </div>
  <div class="swatch swatch--gradient" style="left:812px;top:185px;width:308px;height:198px"></div>
</section>

<section class="section section--white-mid">
  <div class="card card--sm card--gold" style="left:70px;top:201px">
    <div class="brand-name">LichtkanteStudio</div>
    <div class="website">WWW.LICHTKANTESTUDIO.EXAMPLE</div>
  </div>
  <div class="card card--sm card--gold" style="left:437px;top:201px">
    <div class="signature" role="img" aria-label="Handschriftliche Unterschrift Jonas Kerbel"></div>
    <div class="role-title">AUTOMOTIVE PHOTOGRAPHER</div>
    <div class="divider"></div>
    <ul class="contact-list">
      <li class="contact-item"><svg><use href="#icon-home"/></svg><span>17389 Uckerfeld, Brandenburg</span></li>
      <li class="contact-item"><svg><use href="#icon-phone"/></svg><span>0157 / 38214650</span></li>
      <li class="contact-item"><svg><use href="#icon-mail"/></svg><span>lichtkante.studio@postfach.example</span></li>
      <li class="contact-item"><svg><use href="#icon-dot"/></svg><span>Lichtkante_Studio</span></li>
    </ul>
  </div>
  <div class="swatch swatch--flat" style="left:812px;top:201px;width:308px;height:198px"></div>
</section>

<section class="section section--dark">
  <div class="card card--xl card--scene" style="left:289px;top:151px">
    <div class="brand-name">LichtkanteStudio</div>
    <div class="website">WWW.LICHTKANTESTUDIO.EXAMPLE</div>
  </div>
  <div class="card card--xl card--scene" style="left:289px;top:664px">
    <div class="signature" role="img" aria-label="Handschriftliche Unterschrift Jonas Kerbel"></div>
    <div class="role-title">AUTOMOTIVE PHOTOGRAPHER</div>
    <div class="divider"></div>
    <ul class="contact-list">
      <li class="contact-item"><svg><use href="#icon-home"/></svg><span>17389 Uckerfeld, Brandenburg</span></li>
      <li class="contact-item"><svg><use href="#icon-phone"/></svg><span>0157 / 38214650</span></li>
      <li class="contact-item"><svg><use href="#icon-mail"/></svg><span>lichtkante.studio@postfach.example</span></li>
      <li class="contact-item"><svg><use href="#icon-dot"/></svg><span>Lichtkante_Studio</span></li>
    </ul>
  </div>
</section>

</body>
</html>
```